Create a new business card

I’m looking to update my business card to make it match the rest of my brand. I will include my current website as well as what my vehicle designs look like, etc..
What my business currently services
Weekly maintenance pool openings / closings
Equipment repair, including pumps, heaters, salt systems, filters, etc.
We install automatic covers and maintain them as well as provide preventative maintenance

I would like to include my name.
Dorian Pelkin.
My title
Owner
My email
Dorian@tidewellnx.com
4015827160
Www.tidewellnx.com

```html
<!DOCTYPE html>
<html lang="en">
<head>
<meta charset="utf-8">
<title>Tidewell Pool Care – Business Card</title>
<link rel="stylesheet" href="https://fonts.googleapis.com/css2?family=Oswald:wght@300;400;600&display=swap">
<style>
  :root {
    --navy: #1f2d66;
    --navy-deep: #1a2659;
    --sky: #27ade6;
    --orange: #e2622a;
    --white: #ffffff;
    --backdrop: #e9ebef;
  }
  * { margin: 0; padding: 0; box-sizing: border-box; }
  html, body { width: 1200px; height: 1122px; overflow: hidden; }
  body {
    background: var(--backdrop);
    font-family: "Oswald", "Arial Narrow", sans-serif;
    position: relative;
  }
  .card {
    position: absolute;
    left: 250px;
    width: 700px;
    height: 400px;
    border-radius: 26px;
    overflow: hidden;
    background: var(--navy);
    box-shadow: 0 14px 34px rgba(20, 28, 60, 0.22);
  }
  .card--services { top: 110px; }
  .card--contact { top: 612px; }

  /* Brand name block (used on both sides) */
  .brand {
    position: absolute;
    display: flex;
    align-items: center;
    gap: 14px;
  }
  .brand__dot {
    width: 34px; height: 34px;
    border-radius: 50%;
    background: var(--sky);
    flex: none;
  }
  .brand__name {
    font-weight: 600;
    font-size: 34px;
    line-height: 1.05;
    text-transform: uppercase;
    letter-spacing: 1px;
  }
  .card--services .brand { left: 60px; top: 150px; }
  .card--services .brand__name { color: var(--white); }
  .card--contact .brand { left: 440px; top: 168px; }
  .card--contact .brand__name { color: var(--navy); font-size: 30px; }

  /* Services side */
  .divider {
    position: absolute;
    left: 358px; top: 60px;
    width: 2px; height: 280px;
    background: var(--orange);
  }
  .services {
    position: absolute;
    left: 386px; top: 52px;
    list-style: none;
  }
  .services__item {
    display: flex;
    align-items: center;
    gap: 10px;
    color: var(--white);
    font-weight: 400;
    font-size: 15.5px;
    letter-spacing: 0.8px;
    text-transform: uppercase;
    line-height: 24.6px;
  }
  .tick { width: 15px; height: 15px; flex: none; }

  /* Contact side */
  .swoosh { position: absolute; inset: 0; }
  .person {
    position: absolute;
    left: 56px; top: 70px;
  }
  .person__name {
    color: var(--sky);
    font-weight: 600;
    font-size: 40px;
    letter-spacing: 1px;
    text-transform: uppercase;
    line-height: 1;
  }
  .person__title {
    color: var(--orange);
    font-weight: 400;
    font-size: 19px;
    letter-spacing: 1px;
    text-transform: uppercase;
    margin-top: 6px;
  }
  .contacts {
    position: absolute;
    left: 56px; top: 176px;
    list-style: none;
  }
  .contacts__item {
    display: flex;
    align-items: center;
    gap: 14px;
    color: var(--white);
    font-weight: 300;
    font-size: 21px;
    letter-spacing: 0.6px;
    text-transform: uppercase;
    line-height: 40px;
  }
  .contacts__item--phone { font-weight: 400; font-size: 23px; }
  .icon { width: 20px; height: 20px; flex: none; }
</style>
</head>
<body>

  <!-- Services side -->
  <section class="card card--services">
    <div class="brand">
      <span class="brand__dot"></span>
      <span class="brand__name">Tidewell<br>Pool Care</span>
    </div>
    <div class="divider"></div>
    <ul class="services">
      <li class="services__item"><svg class="tick" viewBox="0 0 16 16"><circle cx="8" cy="8" r="8" fill="var(--sky)"/><path d="M4.5 8.2l2.3 2.3 4.7-4.7" fill="none" stroke="#fff" stroke-width="1.8" stroke-linecap="round" stroke-linejoin="round"/></svg>Weekly pool maintenance</li>
      <li class="services__item"><svg class="tick" viewBox="0 0 16 16"><circle cx="8" cy="8" r="8" fill="var(--sky)"/><path d="M4.5 8.2l2.3 2.3 4.7-4.7" fill="none" stroke="#fff" stroke-width="1.8" stroke-linecap="round" stroke-linejoin="round"/></svg>Pool opening &amp; closing</li>
      <li class="services__item"><svg class="tick" viewBox="0 0 16 16"><circle cx="8" cy="8" r="8" fill="var(--sky)"/><path d="M4.5 8.2l2.3 2.3 4.7-4.7" fill="none" stroke="#fff" stroke-width="1.8" stroke-linecap="round" stroke-linejoin="round"/></svg>Equipment servicing</li>
      <li class="services__item"><svg class="tick" viewBox="0 0 16 16"><circle cx="8" cy="8" r="8" fill="var(--sky)"/><path d="M4.5 8.2l2.3 2.3 4.7-4.7" fill="none" stroke="#fff" stroke-width="1.8" stroke-linecap="round" stroke-linejoin="round"/></svg>Equipment installation</li>
      <li class="services__item"><svg class="tick" viewBox="0 0 16 16"><circle cx="8" cy="8" r="8" fill="var(--sky)"/><path d="M4.5 8.2l2.3 2.3 4.7-4.7" fill="none" stroke="#fff" stroke-width="1.8" stroke-linecap="round" stroke-linejoin="round"/></svg>Structural pool repair</li>
      <li class="services__item"><svg class="tick" viewBox="0 0 16 16"><circle cx="8" cy="8" r="8" fill="var(--sky)"/><path d="M4.5 8.2l2.3 2.3 4.7-4.7" fill="none" stroke="#fff" stroke-width="1.8" stroke-linecap="round" stroke-linejoin="round"/></svg>Plumbing updates &amp; upgrades</li>
      <li class="services__item"><svg class="tick" viewBox="0 0 16 16"><circle cx="8" cy="8" r="8" fill="var(--sky)"/><path d="M4.5 8.2l2.3 2.3 4.7-4.7" fill="none" stroke="#fff" stroke-width="1.8" stroke-linecap="round" stroke-linejoin="round"/></svg>Coping replacement &amp; removal</li>
      <li class="services__item"><svg class="tick" viewBox="0 0 16 16"><circle cx="8" cy="8" r="8" fill="var(--sky)"/><path d="M4.5 8.2l2.3 2.3 4.7-4.7" fill="none" stroke="#fff" stroke-width="1.8" stroke-linecap="round" stroke-linejoin="round"/></svg>Tile replacement &amp; removal</li>
      <li class="services__item"><svg class="tick" viewBox="0 0 16 16"><circle cx="8" cy="8" r="8" fill="var(--sky)"/><path d="M4.5 8.2l2.3 2.3 4.7-4.7" fill="none" stroke="#fff" stroke-width="1.8" stroke-linecap="round" stroke-linejoin="round"/></svg>Interior resurfacing/replastering</li>
      <li class="services__item"><svg class="tick" viewBox="0 0 16 16"><circle cx="8" cy="8" r="8" fill="var(--sky)"/><path d="M4.5 8.2l2.3 2.3 4.7-4.7" fill="none" stroke="#fff" stroke-width="1.8" stroke-linecap="round" stroke-linejoin="round"/></svg>Filter system equipment upgrades</li>
      <li class="services__item"><svg class="tick" viewBox="0 0 16 16"><circle cx="8" cy="8" r="8" fill="var(--sky)"/><path d="M4.5 8.2l2.3 2.3 4.7-4.7" fill="none" stroke="#fff" stroke-width="1.8" stroke-linecap="round" stroke-linejoin="round"/></svg>Decking removal &amp; renovation</li>
      <li class="services__item"><svg class="tick" viewBox="0 0 16 16"><circle cx="8" cy="8" r="8" fill="var(--sky)"/><path d="M4.5 8.2l2.3 2.3 4.7-4.7" fill="none" stroke="#fff" stroke-width="1.8" stroke-linecap="round" stroke-linejoin="round"/></svg>Commercial pool services</li>
    </ul>
  </section>

  <!-- Contact side -->
  <section class="card card--contact">
    <svg class="swoosh" viewBox="0 0 700 400" aria-hidden="true">
      <circle cx="612" cy="250" r="284" fill="var(--orange)"/>
      <circle cx="620" cy="258" r="276" fill="var(--navy)"/>
      <circle cx="616" cy="262" r="270" fill="var(--sky)"/>
      <circle cx="624" cy="266" r="262" fill="var(--white)"/>
    </svg>
    <div class="person">
      <h1 class="person__name">Dorian Pelkin</h1>
      <p class="person__title">Owner</p>
    </div>
    <ul class="contacts">
      <li class="contacts__item contacts__item--phone">
        <svg class="icon" viewBox="0 0 24 24"><path d="M6.6 10.8a15.1 15.1 0 0 0 6.6 6.6l2.2-2.2c.3-.3.7-.4 1-.2 1.1.4 2.3.6 3.6.6.6 0 1 .4 1 1V20c0 .6-.4 1-1 1A17 17 0 0 1 3 4c0-.6.4-1 1-1h3.5c.6 0 1 .4 1 1 0 1.3.2 2.5.6 3.6.1.3 0 .7-.2 1z" fill="var(--sky)"/></svg>
        (401) 582-7160
      </li>
      <li class="contacts__item">
        <svg class="icon" viewBox="0 0 24 24"><rect x="2" y="5" width="20" height="14" rx="1.5" fill="var(--sky)"/><path d="M2.5 6l9.5 7 9.5-7" fill="none" stroke="var(--navy)" stroke-width="1.6"/></svg>
        Dorian@tidewellnx.com
      </li>
      <li class="contacts__item">
        <svg class="icon" viewBox="0 0 24 24"><circle cx="12" cy="12" r="10" fill="var(--sky)"/><path d="M2 12h20M12 2c3 3 3 17 0 20M12 2c-3 3-3 17 0 20" fill="none" stroke="var(--navy)" stroke-width="1.3"/></svg>
        tidewellnx.com
      </li>
    </ul>
    <div class="brand">
      <span class="brand__dot"></span>
      <span class="brand__name">Tidewell<br>Pool Care</span>
    </div>
  </section>

</body>
</html>
```